Exclusive beauty salon needs a price list or services booklet

I need a new very attractive flyer for my beauty salon, containing information on the different services and their prices.
In attachment you can find a pdf of the "old" one, but I'd love to have a beautifully designed new one!
I'd love to have a booklet in format 148 x 148 mm, or in US format, containing 12 or 16 pages, but if you can offer other nice looking designs they are welcome!
The services that need to come in the booklet with their prices can all be found on my website: www.atelierverano.be, starting with
Gelaatsverzorging
Wimperverlenging
Suikerontharing
Wimperlifting
Permanente Make Up
Airbrush Tanning

Target Market(s)

woman from 20 to 89 years old

Industry/Entity Type

Beauty Salon

Font styles to use
Sans Serif

Colors

Designer to choose colors to be used in the design.

Requirements
Must have
• a classy nice look, it must contain details about the services from my beauty salon and their prices, and nice pictures.
• The Names, prices and explanations of the services can easily be found on my website: www.atelierverano.be
Nice to have
• In attachment you can find the "old" price list in pdf, what I need now is a "new booklet" with the new logo and updated services price list.
• I need a very nice and attractive looking booklet, classy chique, Paris chique, looking very expensive.
Should not have
• Not too much colors, not too curly, but still feminine

```html
<!DOCTYPE html>
<html lang="nl">
<head>
<meta charset="utf-8">
<title>Permanente make up – prijslijst</title>
<link rel="stylesheet" href="https://fonts.googleapis.com/css2?family=Questrial&display=swap">
<style>
  :root {
    --backdrop: #a9a9a9;
    --paper: #ffffff;
    --paper-shade: #ededed;
    --rose: #e3bcc1;
    --rose-title: #d79aa3;
    --teal: #94d1cb;
    --text-grey: #8c8c8c;
    --rule-blue: #9cc8da;
    --photo-dark: #1c1816;
    --photo-skin: #b88d7c;
  }
  * { margin: 0; padding: 0; box-sizing: border-box; }
  html, body {
    width: 1200px; height: 523px; overflow: hidden;
    background: var(--backdrop);
    font-family: "Questrial", "Century Gothic", sans-serif;
  }
  .spread {
    position: absolute; left: 252px; top: 82px;
    width: 672px; height: 348px;
    display: flex;
    box-shadow: 0 2px 6px rgba(0,0,0,.18);
  }
  .page { position: relative; width: 336px; height: 348px; background: var(--paper); }
  .page--left { background: linear-gradient(to right, var(--paper) 85%, var(--paper-shade)); }
  .page--right { background: linear-gradient(to right, var(--paper-shade), var(--paper) 12%); }

  .page-title {
    position: absolute; right: 18px; top: 15px;
    font-size: 13px; font-weight: 400; letter-spacing: .3px;
    color: var(--rose-title); text-transform: uppercase;
  }
  .hero-photo {
    position: absolute; left: 0; top: 40px; width: 336px; height: 158px;
    background: radial-gradient(ellipse 34% 70% at 50% 45%, var(--photo-skin), #6e5045 60%, var(--photo-dark) 95%);
  }
  .consult {
    position: absolute; left: 66px; top: 226px; width: 200px;
    border-left: 1px solid var(--rule-blue);
    padding-left: 11px;
  }
  .consult__heading {
    font-size: 9px; font-weight: 400; color: var(--text-grey);
    text-transform: uppercase; letter-spacing: .2px; line-height: 17px;
  }
  .consult__body {
    position: relative; left: -11px; margin-left: 0; padding-left: 11px;
    margin-top: 4px;
    font-size: 8.3px; line-height: 13.2px; color: var(--text-grey);
  }

  .price-list { position: absolute; left: 24px; top: 28px; width: 312px; list-style: none; }
  .price-item {
    display: flex; justify-content: space-between; align-items: center;
    height: 13px; margin-bottom: 24.4px;
    padding: 0 28px 0 11px;
    color: #fff; font-size: 9.6px; line-height: 13px;
  }
  .price-item--rose { background: linear-gradient(to right, var(--rose) 70%, #e9c6ca); }
  .price-item--teal { background: var(--teal); }
  .price-item__amount { font-size: 7.5px; letter-spacing: .3px; }

  .brand-mark {
    position: absolute; right: 18px; bottom: 22px;
    font-size: 7px; letter-spacing: 2px; color: #555;
    text-transform: uppercase;
  }
</style>
</head>
<body>
  <div class="spread">
    <section class="page page--left">
      <h1 class="page-title">Permanente make up</h1>
      <div class="hero-photo" role="img" aria-label="Close-up portret van een vrouw met neergeslagen ogen en verzorgde wenkbrauwen en lippen"></div>
      <div class="consult">
        <h2 class="consult__heading">Gratis adviesgesprek</h2>
        <p class="consult__body">Het is mogelijk om eerst op consult te komen om te bespreken wat je graag zou willen. De gewenste vorm van uw wenkbrauwen, lippen of eyeliner word samen uitgetekend, we zoeken dan samen de kleur uit die jou gezicht het beste ophaalt en het mooiste bij je past, zodat je een idee krijgt van het resultaat.</p>
      </div>
    </section>
    <section class="page page--right">
      <ul class="price-list">
        <li class="price-item price-item--rose"><span>Full lips</span><span class="price-item__amount">€595</span></li>
        <li class="price-item price-item--teal"><span>Permanente make up volledige oogcontour</span><span class="price-item__amount">€360</span></li>
        <li class="price-item price-item--rose"><span>Brede eyeliner boven het oog</span><span class="price-item__amount">€235</span></li>
        <li class="price-item price-item--teal"><span>Fijne eyeliner boven (wimperinvulling) het oog</span><span class="price-item__amount">€186</span></li>
        <li class="price-item price-item--rose"><span>Wenkbrauwen hairstroke techniek</span><span class="price-item__amount">€320</span></li>
        <li class="price-item price-item--teal"><span>Wenkbrauwen shading brow of poederwenkbrauw</span><span class="price-item__amount">€320</span></li>
        <li class="price-item price-item--rose"><span>Wenkbrauwen power brow</span><span class="price-item__amount">€320</span></li>
      </ul>
      <div class="brand-mark">Atelier Verano</div>
    </section>
  </div>
</body>
</html>
```